Workshop PPT Update for AI Transformation Sessions

Our strategic consulting firm runs strategy workshops using slides as workshop exercises. These slides are used to communicate to the participants in advance, run the workshops and produce the final deliverable.

It is time for a design "upgrade". We'd like them to be more engaging, hipper and more interesting. These slides are utilitarian, so clean and usable is good. I have attached the example of what we have today. I have also attached an example of another company's slides that I like.

We can't rip off their design nor can we go away 100% from what we have. But I think it is possible to "update" our look to something closer to their look. Grey colors are fine with some color pop.

Slide styles needed are - 1) Cover Page, 2) Instructions Page, 3) Bullet list 4) Worksheet (place for participants to add content 5) Table, 6) Two column.

```html
<!DOCTYPE html>
<html lang="en">
<head>
<meta charset="utf-8">
<title>NorthPath – AI Transformation Workshop Slides</title>
<link href="https://fonts.googleapis.com/css2?family=Montserrat:wght@400;500;600;700;800&display=swap" rel="stylesheet">
<style>
  :root{
    --stage:#4a4a4a;
    --slide:#f0f0f0;
    --slide-edge:#e6e6e6;
    --red:#b5443f;
    --red-dark:#8f2f2c;
    --pink:#e9c9c7;
    --ink:#1f1d24;
    --navy:#231f2b;
    --text:#2d2d2d;
    --muted:#555;
    --card:#ffffff;
    --row-alt:#f6f6f6;
  }
  *{box-sizing:border-box;margin:0;padding:0}
  html,body{width:1200px;height:4043px;overflow:hidden;background:var(--stage)}
  body{font-family:"Montserrat",sans-serif;color:var(--text);position:relative}
  .slide{position:absolute;left:41px;width:1120px;height:630px;overflow:hidden;
    background:linear-gradient(135deg,#f7f7f7 0%,var(--slide) 55%,var(--slide-edge) 100%)}
  .brand{position:absolute;display:flex;align-items:center;gap:8px;font-weight:500;font-size:32px;color:#3a3a3a;letter-spacing:-0.5px}
  .brand .dot{width:16px;height:16px;border-radius:50%;background:var(--red)}
  .brand-tr{right:40px;top:35px}
  .photo{position:absolute}
  h2.title{position:absolute;font-weight:700;font-size:36px;color:var(--ink);line-height:1}
  .ticks{list-style:none;position:absolute}
  .ticks li{display:flex;align-items:center;gap:10px}
  .ticks svg{flex:none}
  .num{position:absolute;border-radius:50%;color:#fff;font-weight:700;display:flex;align-items:center;justify-content:center;box-shadow:0 4px 10px rgba(0,0,0,.15)}
  .num.red{background:var(--red)}
  .num.dark{background:var(--navy)}
  .card{position:absolute;background:var(--card);border-radius:4px;box-shadow:0 3px 12px rgba(0,0,0,.06)}
  .card h4{font-weight:700;color:var(--ink)}
  .card p{color:var(--muted);line-height:1.45}

  /* cover */
  .cover-brand{left:64px;top:220px}
  .cover-title{position:absolute;left:64px;top:276px;font-weight:800;font-size:46px;color:var(--ink)}
  .cover-sub{position:absolute;left:64px;top:333px;font-size:34px;line-height:49px;color:var(--ink);font-weight:400}

  /* getting started */
  .gs-list{left:657px;top:209px}
  .gs-list li{font-size:18px;font-weight:700;color:var(--red);height:36px}

  /* table */
  .plan-table{position:absolute;left:52px;top:154px;width:1020px;border-collapse:collapse;font-size:14px;box-shadow:0 3px 14px rgba(0,0,0,.07)}
  .plan-table thead th{background:var(--red);color:#fff;font-weight:700;text-align:left;height:56px;font-size:14px;padding:0}
  .plan-table thead th:first-child{border-top-left-radius:6px}
  .plan-table thead th:last-child{border-top-right-radius:6px}
  .plan-table td{vertical-align:middle;padding:0;color:var(--text)}
  .plan-table tbody tr:nth-child(odd){background:#fff}
  .plan-table tbody tr:nth-child(even){background:var(--row-alt)}
  .plan-table .lvl{font-weight:700;padding-left:15px}
  .plan-table .plan{font-weight:700}

  /* workshop overview */
  .wo-panel{position:absolute;left:0;top:0}
  .wo-heading{position:absolute;left:40px;top:36px;color:#fff;font-weight:800;font-size:31px;line-height:44px;white-space:nowrap}
  .wo-circle{position:absolute;left:113px;top:129px;width:204px;height:204px;border-radius:50%;background:#fff;
    display:flex;align-items:center;justify-content:center;text-align:center;color:var(--red);font-weight:700;font-size:21px;line-height:27px;box-shadow:0 6px 20px rgba(0,0,0,.12)}
  .prep-title{position:absolute;left:129px;top:358px;font-weight:700;font-size:30px;color:var(--ink)}
  .prep-list{left:130px;top:414px}
  .prep-list li{font-size:16px;height:33px;color:var(--text)}
  .flow-title{position:absolute;left:342px;top:38px;font-weight:800;font-size:30px;color:var(--ink)}
  .flow .card{padding:16px 14px 12px 52px}
  .flow .card h4{font-size:17px;line-height:22px}
  .flow .card p{font-size:10.5px;margin-top:6px}
  .flow .num{width:62px;height:62px;font-size:22px}

  /* guiding principles instructions */
  .gp-title{left:35px;top:24px;font-size:36px}
  .instr{position:absolute;left:361px;top:83px;font-weight:700;font-size:15px;color:var(--ink)}
  .steps .card{display:flex;flex-direction:column;justify-content:center;padding-left:40px;padding-right:14px}
  .steps .card h4{font-size:14px}
  .steps .card p{font-size:10px;margin-top:4px}
  .steps .num{width:50px;height:50px;font-size:18px}
  .purpose{position:absolute;left:796px;top:107px;width:188px;height:188px;border-radius:50%;background:#fff;text-align:center;
    display:flex;flex-direction:column;align-items:center;justify-content:center;box-shadow:0 6px 20px rgba(0,0,0,.08)}
  .purpose strong{color:var(--red);font-size:22px;font-weight:700}
  .purpose span{font-size:11px;line-height:17px;color:var(--muted);margin-top:6px;width:150px}
  .mat-title{position:absolute;left:788px;top:322px;font-weight:700;font-size:20px;color:var(--ink)}
  .mat-list{left:790px;top:368px}
  .mat-list li{font-size:15px;height:32px;color:var(--text)}
  .insp{position:absolute;left:791px;font-size:17px;color:var(--ink)}
  .insp.b{font-weight:700}

  /* principles worksheet */
  .ws-panel{position:absolute;left:0;top:0;width:336px;height:630px;background:var(--navy)}
  .ws-vert{position:absolute;left:105px;top:323px;transform:translate(-50%,-50%) rotate(-90deg);white-space:nowrap;color:#fff;font-weight:800;font-size:36px}
  .ws-vert-sub{position:absolute;left:143px;top:323px;transform:translate(-50%,-50%) rotate(-90deg);white-space:nowrap;color:#fff;font-weight:600;font-size:13px}
  .principles .card{left:320px;width:457px;height:86px;padding:16px 10px 0 32px}
  .principles .card h4{font-size:15px}
  .principles .card p{font-size:8.3px;margin-top:7px;white-space:nowrap}
  .principles .num{left:263px;width:60px;height:60px;font-size:21px}
  .principles .num.dark{border:2px solid rgba(255,255,255,.55)}
</style>
</head>
<body>

<svg width="0" height="0" style="position:absolute">
  <symbol id="tick" viewBox="0 0 20 20">
    <circle cx="10" cy="10" r="10" fill="#b5443f"/>
    <path d="M5.5 10.3l3 3 6-6.3" fill="none" stroke="#fff" stroke-width="2.4" stroke-linecap="round" stroke-linejoin="round"/>
  </symbol>
</svg>

<!-- Cover -->
<section class="slide" style="top:39px">
  <div class="photo" role="img" aria-label="Photo of a smiling professional woman in an office, framed by a large red curved shape"
       style="left:520px;top:0;width:600px;height:630px;border-radius:300px 0 0 300px;background:linear-gradient(150deg,#c15a52 0%,#a33d39 45%,#7f2a28 100%)"></div>
  <div class="brand cover-brand"><span class="dot"></span>NorthPath</div>
  <h1 class="cover-title">Kickoff &amp; Discovery</h1>
  <p class="cover-sub">Sizing &amp; Scoping AI<br>Transformation</p>
</section>

<!-- Getting Started -->
<section class="slide" style="top:706px">
  <div class="photo" role="img" aria-label="Photo of hands holding a tablet showing business charts"
       style="left:0;top:202px;width:284px;height:428px;background:linear-gradient(160deg,#3d4656 0%,#6b7a8c 50%,#c9d2dc 100%)"></div>
  <div class="photo" role="img" aria-label="Photo of a team gathered around a table reviewing documents in a bright office"
       style="left:306px;top:0;width:314px;height:370px;border-radius:0 0 40px 40px;background:linear-gradient(170deg,#d9d9d6 0%,#a9a39d 50%,#5d4a44 100%)"></div>
  <div class="brand brand-tr"><span class="dot"></span>NorthPath</div>
  <h2 class="title" style="left:657px;top:140px">Getting Started</h2>
  <ul class="ticks gs-list">
    <li><svg width="14" height="14"><use href="#tick"/></svg>Complete the Engagement Sizing Survey.</li>
    <li><svg width="14" height="14"><use href="#tick"/></svg>Collect relevant inputs.</li>
    <li><svg width="14" height="14"><use href="#tick"/></svg>Determine workshop participants &amp; date.</li>
    <li><svg width="14" height="14"><use href="#tick"/></svg>Send invites, to include pre-work.</li>
  </ul>
</section>

<!-- Plan Structure -->
<section class="slide" style="top:1371px">
  <h2 class="title" style="left:55px;top:50px">Plan Structure</h2>
  <div class="brand brand-tr"><span class="dot"></span>NorthPath</div>
  <table class="plan-table">
    <colgroup><col style="width:101px"><col style="width:155px"><col style="width:244px"><col style="width:256px"><col style="width:264px"></colgroup>
    <thead>
      <tr><th style="padding-left:55px" colspan="2">Level Planning</th><th>Element &amp; Definition</th><th>Accountability/Owner</th><th>Frequency of Modification</th></tr>
    </thead>
    <tbody>
      <tr style="height:85px"><td class="lvl">1</td><td class="plan">What<br>(overall)</td><td>Strategic Priorities</td><td>N/A</td><td>3+ years</td></tr>
      <tr style="height:67px"><td class="lvl">1.1</td><td class="plan">What<br>(this year)</td><td>Goals<br>Outcomes &amp; Strategies</td><td>Executive Leadership</td><td>1-3 years</td></tr>
      <tr style="height:71px"><td class="lvl">1.1.1</td><td class="plan">How</td><td>Key Performance Indicators<br>and/or Initiatives</td><td></td><td>1 year<br>(w/ qrtly targets)</td></tr>
      <tr style="height:57px"><td class="lvl">1.1.1.1</td><td class="plan">How</td><td>Action Items</td><td></td><td>Quarterly/Monthly</td></tr>
    </tbody>
  </table>
</section>

<!-- Workshop Overview -->
<section class="slide" style="top:2036px">
  <svg class="wo-panel" width="280" height="630"><polygon points="0,0 262,0 25,630 0,630" fill="#231f2b"/></svg>
  <h2 class="wo-heading">Workshop<br>Overview</h2>
  <div class="wo-circle">Participants:<br>Execs Duration:<br>2 hrs.</div>
  <h3 class="prep-title">Prep Work:</h3>
  <ul class="ticks prep-list">
    <li><svg width="11" height="11"><use href="#tick"/></svg>Org Strategy</li>
    <li><svg width="11" height="11"><use href="#tick"/></svg>2023 Goal Performance</li>
    <li><svg width="11" height="11"><use href="#tick"/></svg>Existing policies</li>
    <li><svg width="11" height="11"><use href="#tick"/></svg>Pre-thinking questions</li>
  </ul>
  <h2 class="flow-title">Workshop Flow</h2>
  <div class="brand brand-tr"><span class="dot"></span>NorthPath</div>
  <div class="flow">
    <div class="card" style="left:391px;top:111px;width:379px;height:109px"><h4>Confirm Company Direction</h4><p>Recap organizational purpose, values, vision &amp;<br>winning strategy.</p></div>
    <div class="num red" style="left:361px;top:135px">01</div>
    <div class="card" style="left:391px;top:235px;width:379px;height:73px;padding-top:24px"><h4>Develop AI Vision</h4></div>
    <div class="num dark" style="left:361px;top:241px">02</div>
    <div class="card" style="left:391px;top:323px;width:379px;height:108px"><h4>Agree on a Governance Approach</h4><p>Developed AI Guiding Principles, supporting<br>policies to include approved tools.</p></div>
    <div class="num red" style="left:361px;top:346px">03</div>
    <div class="card" style="left:391px;top:453px;width:379px;height:121px;padding-top:20px"><h4>Agree on a Governance Approach</h4><p>Set approach to training &amp; continuous<br>learning.</p></div>
    <div class="num dark" style="left:361px;top:474px">04</div>
    <div class="card" style="left:817px;top:111px;width:272px;height:121px"><h4>Agree on a Training<br>&amp; Learning Approach</h4><p>Set approach to training &amp;<br>continuous learning.</p></div>
    <div class="num red" style="left:789px;top:135px">05</div>
    <div class="card" style="left:817px;top:258px;width:272px;height:124px"><h4>Determine Rollout<br>&amp; Communication</h4><p>Organizational rollout &amp; continuous<br>communication.</p></div>
    <div class="num dark" style="left:789px;top:286px">06</div>
  </div>
</section>

<!-- Creating AI Guiding Principles -->
<section class="slide" style="top:2703px">
  <div class="photo" role="img" aria-label="Close-up photo of a compass-style dial with the word strategy"
       style="left:0;top:105px;width:317px;height:525px;border-radius:0 260px 0 0;background:radial-gradient(circle at 20% 60%,#f4efe8 0%,#d9d2c8 45%,#8f8a84 100%)"></div>
  <h2 class="title gp-title">Creating your AI Guiding Principles</h2>
  <div class="brand brand-tr"><span class="dot"></span>NorthPath</div>
  <p class="instr">Instructions:</p>
  <div class="steps">
    <div class="card" style="left:391px;top:117px;width:293px;height:82px"><h4>Create the Outline</h4><p>Determine the topics that need a principle.</p></div>
    <div class="num red" style="left:355px;top:132px">01</div>
    <div class="card" style="left:391px;top:219px;width:293px;height:82px"><h4>Audit the Outline</h4><p>Look at the current policies to determine if all<br>topics are covered</p></div>
    <div class="num dark" style="left:355px;top:234px">02</div>
    <div class="card" style="left:391px;top:323px;width:300px;height:56px"><h4>Draft the Guiding Principles.</h4></div>
    <div class="num red" style="left:355px;top:326px">03</div>
    <div class="card" style="left:391px;top:403px;width:404px;height:56px"><h4>Determine which GPs need detailed policies.</h4></div>
    <div class="num dark" style="left:355px;top:406px">04</div>
    <div class="card" style="left:391px;top:480px;width:404px;height:56px"><h4>Determine which AI Tools support the GPs.</h4></div>
    <div class="num red" style="left:355px;top:483px">05</div>
    <div class="card" style="left:391px;top:559px;width:384px;height:56px"><h4>Finalize via a legal and executive review.</h4></div>
    <div class="num dark" style="left:355px;top:562px">06</div>
  </div>
  <div class="purpose"><strong>Purpose:</strong><span>To create behavioral statements that everyone is expected to adhere to.</span></div>
  <h3 class="mat-title">Your Existing Material</h3>
  <ul class="ticks mat-list">
    <li><svg width="11" height="11"><use href="#tick"/></svg>Company Values</li>
    <li><svg width="11" height="11"><use href="#tick"/></svg>Current Policies (GDPR, CCPA, etc.)</li>
    <li><svg width="11" height="11"><use href="#tick"/></svg>Legal Guidance</li>
    <li><svg width="11" height="11"><use href="#tick"/></svg>OTHER</li>
  </ul>
  <p class="insp b" style="top:516px">Examples for Inspiration</p>
  <p class="insp" style="top:546px">See next slides</p>
  <p class="insp b" style="top:577px">Chatbot Prompts</p>
  <p class="insp" style="top:605px">HERE</p>
</section>

<!-- AI Guiding Principles worksheet -->
<section class="slide" style="top:3371px">
  <div class="ws-panel"></div>
  <h2 class="ws-vert">AI Guiding Principles</h2>
  <p class="ws-vert-sub">What guides our decision-making and approach?</p>
  <div class="brand brand-tr"><span class="dot"></span>NorthPath</div>
  <div class="principles">
    <div class="card" style="top:73px"><h4>Principle #1</h4><p>Complete perspective from Executives, Directors, Managers &amp; Staff. Conduct competitive<br>analysis and customer research (optional).</p></div>
    <div class="num red" style="top:86px">01</div>
    <div class="card" style="top:180px"><h4>Principle #2</h4><p>Complete perspective from Executives, Directors, Managers &amp; Staff. Conduct competitive<br>analysis and customer research (optional)</p></div>
    <div class="num dark" style="top:193px">02</div>
    <div class="card" style="top:285px"><h4>Principle #3</h4><p>Complete perspective from Executives, Directors, Managers &amp; Staff. Conduct competitive<br>analysis and customer research (optional)</p></div>
    <div class="num red" style="top:298px">03</div>
    <div class="card" style="top:392px"><h4>Principle #4</h4><p>Complete perspective from Executives, Directors, Managers &amp; Staff. Conduct competitive<br>analysis and customer research (optional)</p></div>
    <div class="num dark" style="top:405px">04</div>
    <div class="card" style="top:497px"><h4>Principle #5</h4><p>Complete perspective from Executives, Directors, Managers &amp; Staff. Conduct competitive<br>analysis and customer research (optional).</p></div>
    <div class="num red" style="top:510px">05</div>
  </div>
</section>

</body>
</html>
```